1" x 3" label needed for essential oil bottle(s) - new ecommerce company

We need a label designed for 10 ml bottles of essential oils. We are offering 9 different types of essential oil: Lavender, Cedarwood, Eucalyptus, Frankincense, Lemon, Orange, Peppermint, Rosemary, and Tea Tree. The label should have a space for the type of essential oil. The bottles are an amber color (am including a photo) as essential oils are sensitive to light. also am including an AI file of our logo, which we'd like included on the label; the logo file also contains our logo colors, a dark blue and light grey. We'd also like the following on the label: "CAUTION: EYE AND SKIN IRRITANT. Avoid contact with eyes and skin. Wash hands after handling. If eye contact occurs, flush with water for 15 minutes. Not intended for topical or internal use. Contains Essential Oils. KEEP OUT OF REACH OF CHILDREN."
Also "Ingredients: 100% pure essential oil, GC tested."
Also "0.33 fl oz (10 ml)
Finally, we will need to include a sideways bar code on the right side of the label, so need 3/8" of white space on the right of the label.
We'd like the label to be calming, but modern, friendly, and confident.

```html
<!DOCTYPE html>
<html lang="en">
<head>
<meta charset="utf-8">
<title>Solavera Essential Oil Labels</title>
<link rel="stylesheet" href="https://fonts.googleapis.com/css2?family=Marcellus&family=Montserrat:wght@400;500;600;700&display=swap">
<style>
  :root {
    --page: #e8e6ea;
    --label: #f7f2ea;
    --ink: #4a4a4a;
    --brand-ink: #555555;
    --rule: #d9d1c4;
    --cedar: #1f9a3a;
    --cedar-leaf: #6fae6a;
    --lavender: #b47fd2;
    --lavender-leaf: #8a6aa8;
    --orange: #f7941d;
    --orange-leaf: #f2a65a;
  }
  * { box-sizing: border-box; margin: 0; padding: 0; }
  html, body {
    width: 1200px;
    height: 900px;
    overflow: hidden;
    background: var(--page);
  }
  .sheet {
    width: 1200px;
    height: 900px;
    display: flex;
    flex-direction: column;
    align-items: center;
    justify-content: center;
    gap: 20px;
  }
  .label {
    width: 810px;
    height: 270px;
    background: var(--label);
    border-radius: 4px;
    box-shadow: 0 2px 10px rgba(0, 0, 0, 0.08);
    display: flex;
    align-items: stretch;
    overflow: hidden;
  }
  .back-panel {
    width: 250px;
    padding: 18px 16px 16px 20px;
    display: flex;
    flex-direction: column;
    justify-content: center;
    gap: 10px;
    border-right: 1px solid var(--rule);
    font-family: "Montserrat", sans-serif;
    color: var(--ink);
  }
  .caution {
    font-size: 9.5px;
    line-height: 1.4;
  }
  .caution strong, .ingredients strong { font-weight: 700; }
  .ingredients {
    font-size: 9.5px;
    line-height: 1.4;
  }
  .front-panel {
    flex: 1;
    padding: 0 18px;
    display: flex;
    flex-direction: column;
    align-items: center;
    justify-content: center;
  }
  .brand-row {
    display: flex;
    align-items: flex-end;
    justify-content: space-between;
    width: 100%;
  }
  .botanical {
    width: 44px;
    height: 84px;
    border-radius: 22px 22px 6px 6px;
  }
  .brand {
    display: flex;
    flex-direction: column;
    align-items: center;
    gap: 10px;
    padding-bottom: 2px;
  }
  .brand-dot {
    width: 28px;
    height: 28px;
    border: 1.5px solid var(--brand-ink);
    border-radius: 50%;
  }
  .brand-name {
    font-family: "Marcellus", serif;
    font-size: 28px;
    letter-spacing: 5px;
    color: var(--brand-ink);
  }
  .oil-band {
    width: 100%;
    margin-top: 6px;
    padding: 5px 0;
    text-align: center;
    font-family: "Montserrat", sans-serif;
    font-weight: 600;
    font-size: 26px;
    letter-spacing: 2px;
    color: #ffffff;
  }
  .oil-details {
    margin-top: 10px;
    text-align: center;
    font-family: "Montserrat", sans-serif;
    font-size: 12px;
    line-height: 1.7;
    color: var(--ink);
  }
  .barcode-space {
    width: 101px;
    flex-shrink: 0;
    background: #ffffff;
    border-left: 1px solid var(--rule);
  }
  .cedarwood .oil-band { background: var(--cedar); }
  .cedarwood .botanical { background: linear-gradient(180deg, var(--cedar-leaf), #3f8a4a); }
  .lavender .oil-band { background: var(--lavender); }
  .lavender .botanical { background: linear-gradient(180deg, var(--lavender-leaf), #5f8a55); }
  .orange .oil-band { background: var(--orange); }
  .orange .botanical { background: linear-gradient(180deg, var(--orange-leaf), #4f9a4a); }
</style>
</head>
<body>
<main class="sheet">
  <section class="label cedarwood">
    <div class="back-panel">
      <p class="caution"><strong>CAUTION: EYE AND SKIN IRRITANT.</strong> Avoid contact with eyes and skin. Wash hands after handling. If eye contact occurs, flush with water for 15 minutes. Not intended for topical or internal use. Contains Essential Oils. <strong>KEEP OUT OF REACH OF CHILDREN.</strong></p>
      <p class="ingredients"><strong>Ingredients:</strong> 100% pure essential oil, GC tested.</p>
    </div>
    <div class="front-panel">
      <div class="brand-row">
        <div class="botanical" role="img" aria-label="Illustration of cedar sprigs"></div>
        <div class="brand">
          <span class="brand-dot"></span>
          <span class="brand-name">SOLAVERA</span>
        </div>
        <div class="botanical" role="img" aria-label="Illustration of cedar sprigs"></div>
      </div>
      <div class="oil-band">CEDARWOOD</div>
      <p class="oil-details">100% pure essential oil<br>0.33 fl oz (10 ml)</p>
    </div>
    <div class="barcode-space" aria-label="Space reserved for barcode"></div>
  </section>

  <section class="label lavender">
    <div class="back-panel">
      <p class="caution"><strong>CAUTION: EYE AND SKIN IRRITANT.</strong> Avoid contact with eyes and skin. Wash hands after handling. If eye contact occurs, flush with water for 15 minutes. Not intended for topical or internal use. Contains Essential Oils. <strong>KEEP OUT OF REACH OF CHILDREN.</strong></p>
      <p class="ingredients"><strong>Ingredients:</strong> 100% pure essential oil, GC tested.</p>
    </div>
    <div class="front-panel">
      <div class="brand-row">
        <div class="botanical" role="img" aria-label="Illustration of lavender stems"></div>
        <div class="brand">
          <span class="brand-dot"></span>
          <span class="brand-name">SOLAVERA</span>
        </div>
        <div class="botanical" role="img" aria-label="Illustration of lavender stems"></div>
      </div>
      <div class="oil-band">LAVENDER</div>
      <p class="oil-details">100% pure essential oil<br>0.33 fl oz (10 ml)</p>
    </div>
    <div class="barcode-space" aria-label="Space reserved for barcode"></div>
  </section>

  <section class="label orange">
    <div class="back-panel">
      <p class="caution"><strong>CAUTION: EYE AND SKIN IRRITANT.</strong> Avoid contact with eyes and skin. Wash hands after handling. If eye contact occurs, flush with water for 15 minutes. Not intended for topical or internal use. Contains Essential Oils. <strong>KEEP OUT OF REACH OF CHILDREN.</strong></p>
      <p class="ingredients"><strong>Ingredients:</strong> 100% pure essential oil, GC tested.</p>
    </div>
    <div class="front-panel">
      <div class="brand-row">
        <div class="botanical" role="img" aria-label="Illustration of orange blossoms and fruit"></div>
        <div class="brand">
          <span class="brand-dot"></span>
          <span class="brand-name">SOLAVERA</span>
        </div>
        <div class="botanical" role="img" aria-label="Illustration of orange blossoms and fruit"></div>
      </div>
      <div class="oil-band">ORANGE</div>
      <p class="oil-details">100% pure essential oil<br>0.33 fl oz (10 ml)</p>
    </div>
    <div class="barcode-space" aria-label="Space reserved for barcode"></div>
  </section>
</main>
</body>
</html>
```